Need App for Impact Related Events

My app is to help with internal events. When you enter the prompted event code the next screen shows you everyone currently at the event. It will give you the ability to Start a conversation with someone you met at that event, or signal it is your turn to send a message. The next screen is a message thread with that person. I am looking for a design that incorporates the colors and ‘feel good’ emotion of our logo. I have pieced together a pretty good interpretation of what I’m looking for in the attached mockup by slicing and dicing designs. I also attached our logo mascot.Screens (see attached mockups)

Note 1: I do not like the picture on the screen used in screen one because it makes it seem like a dating app. I attached an alternative photo that can be used or present different ideas.

Note 2: On the login/signup screen (screen 2) I need an additional first and last name for login, you can try to fit this on one login screen or present a two step signup screen where that is presented in the second screen.

READ MOCKUP GUIDELINES UNDER Must Haves

Target Market(s)

People attending internal social impact events

Industry/Entity Type

Charity

Font styles to use
Sans Serif

Colors
86cfc6

Requirements
Must have
• Follow the screen mockups attached to project
• PLEASE READ
• I have provided a relatively close design of what I’m looking for in the mockups. Some screens need to be followed more closely to my design mockup than other. I have listed a guide below how how closely you should follow my mockup design exactly. Overall I would like to see some ideas of incorporating a few accent colors so it doesn’t appear SO Blue. I also attached some app inspiration designs I found from around the web
• Screen Mockup Guideline Follow %
• Screen 1: 65% - mostly on target, would like to see ways to make it not SO Blue and possibly creative places to add some explainer text describing the app
• Screen 2: 50% - general design idea is here, but more open
• Screen 3: 35% - a lot more room for design influence
• Screen 4: 70% - mostly on target, a little room for design influence/color scheme ideas
• Screen 5-6: 25% - a lot of room for design change/ideas/influence
• Screen 7-8: 80% - already very close to what I need, maybe open to slight sizing and color scheme ideas
• Screen 9: 15% - the most open for influence, only the general functionality of the screen is communicated here
Nice to have
• Please Read Mockup Guideline above. In large part I am looking for something to use some nice accent colors so it is not overwhelmingly blue and bring the whole design into a seamless style.
Should not have

```html
<!DOCTYPE html>
<html lang="en">
<head>
<meta charset="UTF-8">
<title>Edit Profile</title>
<link rel="stylesheet" href="https://fonts.googleapis.com/css2?family=Nunito:wght@800;900&family=Nunito+Sans:wght@600;700&family=Roboto:wght@400&display=swap">
<style>
  :root {
    --bg: #ffffff;
    --ink: #22232f;
    --field-text: #3b3e4b;
    --accent: #13c4c8;
    --field-border: #e4e6ea;
    --kb-bg: #fafafa;
    --kb-bar: #eeeeee;
    --kb-key: #333333;
    --kb-hint: #555555;
    --kb-space: #d9d9d9;
    --kb-enter: #3d8be8;
    --photo-light: #c9c9c9;
    --photo-dark: #5a5a5a;
  }
  * { margin: 0; padding: 0; box-sizing: border-box; }
  html, body {
    width: 675px;
    height: 1200px;
    overflow: hidden;
    background: var(--bg);
  }
  .screen {
    position: relative;
    width: 675px;
    height: 1200px;
    overflow: hidden;
    background: var(--bg);
  }
  .back-button {
    position: absolute;
    left: 36px;
    top: 48px;
    width: 28px;
    height: 38px;
  }
  .page-title {
    position: absolute;
    left: 60px;
    top: 156px;
    font-family: "Nunito", sans-serif;
    font-weight: 900;
    font-size: 58px;
    letter-spacing: 0.5px;
    color: var(--ink);
  }
  .avatar {
    position: absolute;
    left: 225px;
    top: 306px;
    width: 236px;
    height: 236px;
    border-radius: 50%;
    background: radial-gradient(circle at 50% 45%, var(--photo-light) 0%, #8f8f8f 55%, var(--photo-dark) 100%);
    box-shadow: 0 6px 18px rgba(0, 0, 0, 0.12);
  }
  .avatar-edit {
    position: absolute;
    left: 388px;
    top: 474px;
    width: 64px;
    height: 64px;
    border-radius: 50%;
    background: var(--accent);
    display: flex;
    align-items: center;
    justify-content: center;
  }
  .name-field {
    position: absolute;
    left: 56px;
    top: 596px;
    width: 562px;
    height: 73px;
    border: 2px solid var(--field-border);
    border-radius: 8px;
    display: flex;
    align-items: center;
    padding: 0 26px 0 26px;
  }
  .name-field .value {
    flex: 1;
    font-family: "Nunito Sans", sans-serif;
    font-weight: 700;
    font-size: 28px;
    color: var(--field-text);
  }
  .keyboard {
    position: absolute;
    left: 0;
    top: 733px;
    width: 675px;
    height: 467px;
    background: var(--kb-bg);
  }
  .keyboard text {
    font-family: "Roboto", sans-serif;
  }
  .kb-suggestion { font-size: 28px; fill: #444444; }
  .kb-letter { font-size: 38px; fill: var(--kb-key); }
  .kb-hint { font-size: 17px; fill: var(--kb-hint); }
  .kb-symbol { font-size: 26px; fill: var(--kb-key); }
</style>
</head>
<body>
<main class="screen">
  <svg class="back-button" viewBox="0 0 28 38" aria-label="Back">
    <path d="M20 4 L6 19 L20 34" fill="none" stroke="var(--accent)" stroke-width="3.5" stroke-linecap="round" stroke-linejoin="round"/>
  </svg>

  <h1 class="page-title">Edit Profile</h1>

  <div class="avatar" role="img" aria-label="Profile photo of the user"></div>
  <div class="avatar-edit" aria-label="Change photo">
    <svg width="34" height="30" viewBox="0 0 34 30">
      <path d="M4 8 H10 L13 4 H21 L24 8 H30 V26 H4 Z" fill="none" stroke="#ffffff" stroke-width="2.5" stroke-linejoin="round"/>
      <circle cx="17" cy="16" r="5.5" fill="none" stroke="#ffffff" stroke-width="2.5"/>
    </svg>
  </div>

  <div class="name-field">
    <span class="value">Daniel Hayes</span>
    <svg width="30" height="30" viewBox="0 0 30 30" aria-label="Edit name">
      <path d="M5 25 L7 18 L20 5 L25 10 L12 23 Z M17 8 L22 13" fill="none" stroke="var(--accent)" stroke-width="2.5" stroke-linejoin="round"/>
    </svg>
  </div>

  <svg class="keyboard" viewBox="0 0 675 467" aria-label="Keyboard">
    <rect x="0" y="0" width="675" height="73" fill="var(--kb-bar)"/>
    <text class="kb-suggestion" x="148" y="47" text-anchor="middle">Hi</text>
    <text class="kb-suggestion" x="336" y="47" text-anchor="middle">Hello</text>
    <text class="kb-suggestion" x="521" y="47" text-anchor="middle">Howdy</text>
    <line x1="238" y1="20" x2="238" y2="54" stroke="#bbbbbb" stroke-width="2"/>
    <line x1="433" y1="20" x2="433" y2="54" stroke="#bbbbbb" stroke-width="2"/>
    <g transform="translate(643 36)" fill="#555555">
      <rect x="-6" y="-16" width="12" height="22" rx="6"/>
      <path d="M-11 0 A11 11 0 0 0 11 0" fill="none" stroke="#555555" stroke-width="2.5"/>
      <rect x="-1.5" y="10" width="3" height="8"/>
    </g>

    <g text-anchor="middle">
      <text class="kb-hint" x="60" y="110">1</text>
      <text class="kb-hint" x="123" y="110">2</text>
      <text class="kb-hint" x="191" y="110">3</text>
      <text class="kb-hint" x="258" y="110">4</text>
      <text class="kb-hint" x="326" y="110">5</text>
      <text class="kb-hint" x="393" y="110">6</text>
      <text class="kb-hint" x="461" y="110">7</text>
      <text class="kb-hint" x="525" y="110">8</text>
      <text class="kb-hint" x="592" y="110">9</text>
      <text class="kb-hint" x="658" y="110">0</text>

      <text class="kb-letter" x="34" y="148">q</text>
      <text class="kb-letter" x="101" y="148">w</text>
      <text class="kb-letter" x="169" y="148">e</text>
      <text class="kb-letter" x="236" y="148">r</text>
      <text class="kb-letter" x="304" y="148">t</text>
      <text class="kb-letter" x="371" y="148">y</text>
      <text class="kb-letter" x="439" y="148">u</text>
      <text class="kb-letter" x="503" y="148">i</text>
      <text class="kb-letter" x="570" y="148">o</text>
      <text class="kb-letter" x="638" y="148">p</text>

      <text class="kb-letter" x="69" y="242">a</text>
      <text class="kb-letter" x="137" y="242">s</text>
      <text class="kb-letter" x="203" y="242">d</text>
      <text class="kb-letter" x="270" y="242">f</text>
      <text class="kb-letter" x="338" y="242">g</text>
      <text class="kb-letter" x="403" y="242">h</text>
      <text class="kb-letter" x="469" y="242">j</text>
      <text class="kb-letter" x="536" y="242">k</text>
      <text class="kb-letter" x="604" y="242">l</text>

      <text class="kb-letter" x="135" y="336">z</text>
      <text class="kb-letter" x="203" y="336">x</text>
      <text class="kb-letter" x="270" y="336">c</text>
      <text class="kb-letter" x="338" y="336">v</text>
      <text class="kb-letter" x="405" y="336">b</text>
      <text class="kb-letter" x="471" y="336">n</text>
      <text class="kb-letter" x="538" y="336">m</text>

      <text class="kb-symbol" x="52" y="418">?123</text>
      <text class="kb-letter" x="135" y="420">,</text>
      <text class="kb-letter" x="540" y="420">.</text>
    </g>

    <g transform="translate(52 323)" fill="#555555">
      <path d="M0 -16 L-16 2 H-7 V12 H7 V2 H16 Z"/>
      <rect x="-10" y="17" width="20" height="3"/>
    </g>
    <g transform="translate(621 323)">
      <path d="M-20 0 L-10 -12 H18 V12 H-10 Z" fill="#555555"/>
      <path d="M-2 -6 L10 6 M10 -6 L-2 6" stroke="var(--kb-bg)" stroke-width="3" stroke-linecap="round"/>
    </g>

    <circle cx="203" cy="409" r="14" fill="none" stroke="#555555" stroke-width="2.5"/>
    <rect x="253" y="388" width="235" height="45" fill="var(--kb-space)"/>

    <circle cx="621" cy="409" r="29" fill="var(--kb-enter)"/>
    <path d="M632 398 V412 H610 M616 405 L609 412 L616 419" fill="none" stroke="#ffffff" stroke-width="3" stroke-linecap="round" stroke-linejoin="round"/>
  </svg>
</main>
</body>
</html>
```